Coastline Premier Retreats Business Card Design

Design a business card for Coastline Premier Retreats. Look at the website for colors and reference. Card should have logo, name, title, office number, mobile number, email, URL and a tagline like, "Luxury Hotel & Resort Email Marketing" (This might change).

https://www.coastlinepremierretreats.example

The rest I will leave up to your imagination.

Contact Information for Business Card

Logo, name, title, office number, mobile number, email, URL and a tagline like, "Luxury Hotel & Resort Email Marketing" (This might change).

```html
<!DOCTYPE html>
<html lang="en">
<head>
<meta charset="utf-8">
<title>Coastline Premier Retreats – Business Card</title>
<link rel="stylesheet" href="https://fonts.googleapis.com/css2?family=Open+Sans:wght@400;600;700;800&display=swap">
<style>
  :root {
    --stage: #262627;
    --card: #1f1f22;
    --card-deep: #1a1a1d;
    --emboss: #2a2a2e;
    --emboss-edge: #141416;
    --orange: #f47421;
    --white: #ffffff;
  }
  * { box-sizing: border-box; margin: 0; padding: 0; }
  html, body {
    width: 1200px; height: 780px; overflow: hidden;
    background: var(--stage);
    font-family: "Open Sans", sans-serif;
  }
  .stage { position: relative; width: 1200px; height: 780px; }

  .card {
    position: absolute;
    top: 236px;
    width: 520px; height: 300px;
    border-radius: 18px;
    background: var(--card);
    box-shadow: 0 4px 0 var(--orange), 0 18px 30px rgba(0,0,0,.55);
    overflow: hidden;
  }
  .card--back { left: 60px; }
  .card--front { left: 620px; }

  /* back side */
  .back-mark {
    position: absolute; inset: 0;
    display: flex; align-items: center; justify-content: center;
    gap: 14px;
  }
  .back-mark__square {
    width: 22px; height: 22px;
    background: var(--emboss);
  }
  .back-mark__name {
    font-weight: 800; font-size: 30px; letter-spacing: .5px;
    color: var(--emboss);
    text-transform: uppercase;
  }

  /* front side */
  .brand {
    position: absolute; left: 30px; top: 34px;
    display: flex; align-items: center; gap: 10px;
  }
  .brand__square { width: 14px; height: 14px; background: var(--orange); }
  .brand__name {
    font-weight: 800; font-size: 17px; letter-spacing: .4px;
    color: var(--white); text-transform: uppercase;
  }

  .person {
    position: absolute; right: 34px; top: 92px;
    text-align: right;
  }
  .person__name { font-weight: 800; font-size: 22px; line-height: 1.1; }
  .person__first { color: var(--orange); }
  .person__last { color: var(--white); }
  .person__title {
    font-weight: 600; font-size: 12px; color: var(--white);
    margin-top: 3px;
  }
  .accent-bar {
    position: absolute; right: 0; top: 88px;
    width: 14px; height: 50px; background: var(--orange);
  }

  .tagline {
    position: absolute; left: 56px; top: 150px;
    font-size: 12px; line-height: 1.3; color: var(--orange);
  }

  .contacts {
    position: absolute; left: 56px; top: 200px;
    list-style: none;
  }
  .contacts li {
    display: flex; align-items: center; gap: 9px;
    font-size: 11.5px; line-height: 20px; color: var(--white);
  }
  .contacts svg { width: 12px; height: 12px; flex: none; }
  .icon { fill: none; stroke: var(--orange); stroke-width: 1.6; stroke-linecap: round; stroke-linejoin: round; }
  .icon-fill { fill: var(--orange); }
</style>
</head>
<body>
<main class="stage">

  <section class="card card--back" aria-label="Card back">
    <div class="back-mark">
      <span class="back-mark__square"></span>
      <span class="back-mark__name">Coastline Premier Retreats</span>
    </div>
  </section>

  <section class="card card--front" aria-label="Card front">
    <div class="brand">
      <span class="brand__square"></span>
      <span class="brand__name">Coastline Premier Retreats</span>
    </div>

    <div class="person">
      <p class="person__name"><span class="person__first">Lena</span> <span class="person__last">Marwick</span></p>
      <p class="person__title">Managing Director</p>
    </div>
    <span class="accent-bar"></span>

    <p class="tagline">Luxury Hotel &amp;<br>Resort Email Marketing</p>

    <ul class="contacts">
      <li>
        <svg viewBox="0 0 16 16" aria-hidden="true"><path class="icon-fill" d="M3.5 1.5l2.5 0 1 3.5-1.8 1.2a8 8 0 0 0 4.6 4.6l1.2-1.8 3.5 1v2.5a1.5 1.5 0 0 1-1.6 1.5A12.5 12.5 0 0 1 2 3.1 1.5 1.5 0 0 1 3.5 1.5z"/></svg>
        (555) 014-2758
      </li>
      <li>
        <svg viewBox="0 0 16 16" aria-hidden="true"><rect class="icon" x="4" y="1.5" width="8" height="13" rx="1.5"/><line class="icon" x1="7" y1="12" x2="9" y2="12"/></svg>
        (555) 019-7777
      </li>
      <li>
        <svg viewBox="0 0 16 16" aria-hidden="true"><circle class="icon" cx="8" cy="8" r="6.5"/><ellipse class="icon" cx="8" cy="8" rx="2.8" ry="6.5"/><line class="icon" x1="1.5" y1="8" x2="14.5" y2="8"/></svg>
        www.coastlinepremierretreats.example
      </li>
      <li>
        <svg viewBox="0 0 16 16" aria-hidden="true"><rect class="icon" x="1.5" y="3.5" width="13" height="9" rx="1"/><polyline class="icon" points="1.5,4 8,9 14.5,4"/></svg>
        info@coastlinepremierretreats.example
      </li>
    </ul>
  </section>

</main>
</body>
</html>
```